Heating and Cooling Company mobile website

We need a website specifically designed for a viewing on a mobile device.

We serve the northern New Jersey heating, cooling and electrical residential market.

The goal is the drive traffic to the site by using Brintel Pay Per click. People will be searching for an HVAC contractor, and they land on our page. They need to get key info quickly without all the clutter of a desktop type of site.

Target Market(s)

Homeowners

Industry/Entity Type

Hvac

Coding

Coded - Design and coding required

Number of Pages Required

5+ page

Font styles to use
Serif

Requirements
Must have
• View attachments to see samples of the desktop version. It must have a similar color scheme
• The copy of the website is also attached
Nice to have
• Would like it to have a sort of Vardok feel to it. Make it seem like its an app that people are using and that its exciting to be on the website. It would be nice to have a page where customers can book appointments

```html
<!DOCTYPE html>
<html lang="en">
<head>
<meta charset="utf-8">
<title>Heating &amp; Cooling News</title>
<link rel="stylesheet" href="https://fonts.googleapis.com/css2?family=Jost:wght@600&family=Figtree:wght@400;500&display=swap">
<style>
  :root {
    --paper: #e8e0cc;
    --photo-light: #e6dfd2;
    --photo-mid: #cfc2ad;
    --photo-dark: #b3a289;
    --navy: #2c3550;
    --ink: #1f1d1a;
    --accent: #9b1b30;
  }
  * { box-sizing: border-box; margin: 0; padding: 0; }
  html, body {
    width: 752px;
    height: 1200px;
    overflow: hidden;
    background: var(--paper);
  }
  .screen {
    position: relative;
    width: 752px;
    height: 1200px;
    overflow: hidden;
    background: var(--paper);
  }
  .hero-photo {
    position: absolute;
    left: 0; top: 0;
    width: 752px;
    height: 385px;
    background:
      radial-gradient(ellipse at 55% 40%, var(--photo-mid) 0%, transparent 65%),
      linear-gradient(180deg, var(--photo-light) 0%, #dcd1be 50%, var(--photo-dark) 100%);
  }
  .news-date {
    position: absolute;
    left: 63px;
    font-family: "Jost", sans-serif;
    font-weight: 600;
    font-size: 36px;
    line-height: 36px;
    letter-spacing: 0.4px;
    color: var(--navy);
    text-transform: uppercase;
  }
  .news-summary {
    position: absolute;
    left: 63px;
    width: 603px;
    font-family: "Figtree", sans-serif;
    font-size: 27px;
    line-height: 59px;
    color: var(--ink);
    text-align: justify;
  }
  .read-more {
    position: absolute;
    left: 67px;
    top: 795px;
    display: flex;
    align-items: center;
    gap: 16px;
    font-family: "Figtree", sans-serif;
    font-weight: 500;
    font-size: 28px;
    line-height: 36px;
    color: var(--accent);
    text-decoration: none;
    text-transform: uppercase;
  }
  .read-more svg { width: 14px; height: 20px; fill: var(--accent); }
  .first-date { top: 451px; }
  .first-summary { top: 528px; }
  .second-date { top: 967px; }
  .second-summary { top: 1078px; }
</style>
</head>
<body>
  <main class="screen">
    <div class="hero-photo" role="img" aria-label="Sepia photo of a family walking hand in hand along a sandy beach"></div>

    <h2 class="news-date first-date">August 26</h2>
    <p class="news-summary first-summary">Our fall furnace tune-up special is here. Book a safety check now and keep your home warm and efficient before the first cold snap.</p>
    <a class="read-more" href="#">Read more
      <svg viewBox="0 0 14 20" aria-hidden="true"><path d="M0 0 L14 10 L0 20 Z"/></svg>
    </a>

    <h2 class="news-date second-date">July 15</h2>
    <p class="news-summary second-summary">Beat the summer heat with a central air inspection. Our licensed technicians clean coils, test refrigerant and check every part of the system.</p>
  </main>
</body>
</html>
```